Manufacturer's Representative Group needs a clean new Website

We represent and sell a number of suppliers that design and build products used in Biopharmaceutical manufacturing. Our sales region is in the central US. Our customer base is scientific / engineering based - so clean, we organized design with a focus on the products - easy and clear navigation is necessary. We do not sell direct or warehouse product - so e-commerce is not needed. Our customers will use the website for reference on what we do and offer - we will use the site as a platform to present products from each vendor and the home page will be used to capture an overview and draw users deeper into the site. You can view our current site - which needs A LOT of help to get ideas on products represented and types of products

Target Market(s)

Engineers and Pharmaceutical / Bio pharm end users

Industry/Entity Type

E-Commerce

Number of Pages Required

2 page

Font styles to use
Sans Serif

Requirements
Must have
• I need a home page that provides a snapshot of my company and the product lines we represent - then a second page that I can copy as a template for each line I rep as well as for an "About us / contact" page.
• I would like to be able to manage content on the pages so something easy to adjust pictures or add content is a must
• Must use our logo

```html
<!DOCTYPE html>
<html lang="en">
<head>
<meta charset="utf-8">
<title>Northfield Bio</title>
<link href="https://fonts.googleapis.com/css2?family=Open+Sans:wght@400;600;700&display=swap" rel="stylesheet">
<style>
:root{
  --orange:#e8620a;
  --orange-light:#f47a1f;
  --ink:#333;
  --text:#555;
  --muted:#999;
  --footer:#2b2b2b;
  --navy:#1f3a7a;
  --white:#fff;
}
*{margin:0;padding:0;box-sizing:border-box}
html,body{width:942px;height:1200px;overflow:hidden;background:var(--white)}
body{font-family:"Open Sans",sans-serif;color:var(--text)}
.page{position:relative;width:942px;height:1200px;border-top:2px solid var(--orange)}
.abs{position:absolute}
.brand{left:46px;top:24px;display:flex;align-items:center;gap:8px;font-size:30px;font-weight:400;color:var(--navy);letter-spacing:-.5px}
.brand .dot{width:16px;height:16px;border-radius:50%;background:var(--orange)}
.header-contact{right:45px;top:22px;text-align:right;font-size:16px;line-height:24px;color:var(--ink)}
.nav{left:0;top:84px;width:942px;height:40px;background:linear-gradient(var(--orange-light),var(--orange));box-shadow:0 2px 3px rgba(0,0,0,.2)}
.nav a{position:absolute;top:11px;color:var(--white);font-size:13px;text-decoration:none;text-shadow:0 1px 2px rgba(0,0,0,.4);letter-spacing:.3px}
.hero{left:0;top:124px;width:942px;height:320px;background:linear-gradient(160deg,#dfe6f4 0%,#c7d2ea 45%,#e8ecf5 70%,#b9c4de 100%)}
.hero-caption{left:47px;top:266px;height:57px;background:var(--orange);color:var(--white);font-size:19px;line-height:57px;padding:0 16px;white-space:nowrap;letter-spacing:-.2px;text-shadow:0 1px 2px rgba(0,0,0,.3)}
.hero-next{left:867px;top:292px;width:28px;height:28px}
.drop{height:30px;background:radial-gradient(ellipse at top,rgba(0,0,0,.18),rgba(0,0,0,0) 70%)}
.section-title{font-size:19px;font-weight:700;color:var(--orange);letter-spacing:.4px}
.card{width:195px;height:164px;box-shadow:0 1px 3px rgba(0,0,0,.3)}
.card .photo{height:126px}
.card .label{height:38px;background:var(--orange);color:var(--white);font-size:12px;line-height:38px;padding-left:11px;white-space:nowrap;text-shadow:0 1px 1px rgba(0,0,0,.3)}
.about p{font-size:10.5px;line-height:17.6px;margin-bottom:8px;color:var(--text)}
.btn{background:var(--orange);color:var(--white);font-size:10px;font-weight:600;border-radius:3px;text-align:center}
.contact-box{left:592px;top:734px;width:303px;height:185px;background:var(--orange);border-radius:3px}
.contact-box h2{position:absolute;left:19px;top:14px;font-size:19px;color:var(--white);font-weight:600;letter-spacing:.4px}
.field{position:absolute;background:var(--white);font-size:10px;color:var(--muted);padding:7px 8px;white-space:nowrap}
.submit{position:absolute;left:22px;top:154px;width:55px;height:22px;background:#1a1a1a;color:var(--white);font-size:9.5px;line-height:22px;text-align:center;border-radius:3px}
.partner{top:1032px;display:flex;align-items:center;gap:6px;font-size:15px;font-weight:600;color:var(--navy);white-space:nowrap}
.partner i{display:block;width:11px;height:11px;border-radius:50%;background:var(--orange)}
.footer{left:0;top:1112px;width:942px;height:88px;background:var(--footer)}
.footer a{position:absolute;top:26px;font-size:11px;color:#aaa;text-decoration:none}
.footer .copy{position:absolute;left:47px;top:46px;font-size:11px;color:#999}
.social{position:absolute;top:27px;width:24px;height:24px;background:#3a3a3a}
</style>
</head>
<body>
<div class="page">
  <div class="abs brand"><span class="dot"></span>Northfield Bio</div>
  <div class="abs header-contact">info@northfield-bio.com<br>(555) 014-2290</div>

  <nav class="abs nav">
    <a style="left:46px" href="#">HOME</a>
    <a style="left:131px" href="#">ABOUT US</a>
    <a style="left:243px" href="#">PRODUCTS</a>
    <a style="left:360px" href="#">CONTACT US</a>
  </nav>

  <div class="abs hero" role="img" aria-label="Bright modern laboratory with white benches and equipment"></div>
  <div class="abs hero-caption">High quality fluid handling products</div>
  <svg class="abs hero-next" viewBox="0 0 28 28"><circle cx="14" cy="14" r="14" fill="#333" opacity=".85"/><path d="M11 8l6 6-6 6" stroke="#fff" stroke-width="2.4" fill="none"/></svg>
  <div class="abs drop" style="left:150px;top:446px;width:642px"></div>

  <h2 class="abs section-title" style="left:46px;top:483px">FEATURE PRODUCTS</h2>
  <svg class="abs" style="left:855px;top:488px" width="42" height="19" viewBox="0 0 42 19">
    <circle cx="9.5" cy="9.5" r="9" fill="#aaa"/><path d="M13 9.5H6m3-3.5l-3.5 3.5 3.5 3.5" stroke="#fff" stroke-width="2" fill="none"/>
    <circle cx="32.5" cy="9.5" r="9" fill="#aaa"/><path d="M29 9.5h7m-3-3.5l3.5 3.5-3.5 3.5" stroke="#fff" stroke-width="2" fill="none"/>
  </svg>

  <div class="abs card" style="left:47px;top:530px"><div class="photo" role="img" aria-label="Coiled clear tubing on a teal background" style="background:linear-gradient(135deg,#5fd6e0,#1a9fc7 55%,#0b4f72)"></div><div class="label">Sed ut perspiciatis</div></div>
  <div class="abs card" style="left:266px;top:530px"><div class="photo" role="img" aria-label="Loop of translucent hose on a blue background" style="background:radial-gradient(circle at 50% 45%,#6b8fd0,#16306c 75%)"></div><div class="label">Voluptatem accusantium</div></div>
  <div class="abs card" style="left:484px;top:530px"><div class="photo" role="img" aria-label="Cleanroom process equipment with hoses" style="background:linear-gradient(180deg,#c9d0d8,#eef1f4 60%,#9aa2ab)"></div><div class="label">Doloremque laudantium</div></div>
  <div class="abs card" style="left:700px;top:530px"><div class="photo" role="img" aria-label="Red peristaltic pump with digital display" style="background:linear-gradient(120deg,#c0161a,#d9262a 55%,#e8e2d0)"></div><div class="label">Totam rem aperiam</div></div>
  <div class="abs drop" style="left:60px;top:694px;width:170px"></div>
  <div class="abs drop" style="left:279px;top:694px;width:170px"></div>
  <div class="abs drop" style="left:497px;top:694px;width:170px"></div>
  <div class="abs drop" style="left:713px;top:694px;width:170px"></div>

  <section class="abs about" style="left:46px;top:731px;width:510px">
    <h2 class="section-title" style="margin-bottom:21px">ABOUT US</h2>
    <p>Northfield Biosolutions is a distribution channel, licensed partner and manufacturers representative group providing high quality fluid handling products and technical services to the Midwestern biopharmaceutical community.</p>
    <p>With a core staff of experienced professionals and a team approach to all customer needs, we offer over 30 years of cGMP experience in the selection and use of most process consumable products. We're looking forward to working with you!</p>
  </section>
  <div class="abs btn" style="left:47px;top:907px;width:80px;height:33px;line-height:33px">Read More</div>

  <form class="abs contact-box">
    <h2>CONTACT US</h2>
    <div class="field" style="left:22px;top:50px;width:125px;height:25px">Enter Your name</div>
    <div class="field" style="left:160px;top:50px;width:125px;height:25px">Enter Your Mail Id</div>
    <div class="field" style="left:22px;top:84px;width:263px;height:63px">Enter Your Message</div>
    <div class="submit">Submit</div>
  </form>
  <div class="abs drop" style="left:610px;top:919px;width:270px"></div>

  <h2 class="abs section-title" style="left:47px;top:985px">COMPANIES REPRESENTED</h2>
  <div class="abs partner" style="left:47px"><i></i>PureSeal</div>
  <div class="abs partner" style="left:212px">Corvane Polymers</div>
  <div class="abs partner" style="left:372px">Tidewell Pumps</div>
  <div class="abs partner" style="left:520px">Linetra</div>
  <div class="abs partner" style="left:634px"><i></i>Flexora Hose</div>
  <div class="abs partner" style="left:782px"><i></i>Modulux</div>

  <footer class="abs footer">
    <a style="left:47px" href="#">Home</a>
    <a style="left:122px" href="#">About Us</a>
    <a style="left:214px" href="#">Products</a>
    <a style="left:305px" href="#">Contact us</a>
    <div class="copy">©2014 northfield-bio.com. All rights reserved.</div>
    <span class="social" style="left:742px"></span>
    <span class="social" style="left:774px"></span>
    <span class="social" style="left:806px"></span>
    <span class="social" style="left:838px"></span>
    <span class="social" style="left:870px"></span>
  </footer>
</div>
</body>
</html>
```